Wilderness Doc & TV personality personal page

I’m a wilderness and EMS emergency physician with particular sub specialties and a TV show. I need a website to highlight my interviews, teachings, etc... I did buy a number of domains for now.
Topics and things I need: CV (or version) me in the media, picture gallery, actually I sort of really like what dr owen barkley, my colleague has setup plus I have tv show and stuff like that. ridgeway healer dot com

Target Market(s)

EMS, education, commercial products...

Industry/Entity Type

Medical And Science

Coding

Coded - Design and coding required

Number of Pages Required

1 page

Font styles to use
Sans Serif

Colors
f37122
9bcb3c
0556a4
a54499

Requirements
Must have
• Links and photos to news articles and things that mention me that I can add in.
Nice to have
• Maybe some snapshots of lecture reviews or patient thank you notes. Accolades so to speak
• I really appreciate how sharp it is. I would love to see Headings that resemble my friend's at ridgeway healer dot com. Home, experience, consulting, lectures, affiliates, contact... those are main subjects... I think media also and that will have the TV show stuff and articles written about me...then maybe at the bottom of main page also have splits for training, research, television, and maybe exploration
Should not have
• The medical symbol with two snakes... that means quack doctor

```html
<!DOCTYPE html>
<html lang="en">
<head>
<meta charset="utf-8">
<title>Wilderness and EMS Emergency Physician</title>
<link href="https://fonts.googleapis.com/css2?family=Source+Sans+3:wght@400;600;700;900&display=swap" rel="stylesheet">
<style>
:root{
  --blue:#0556a4;
  --blue-deep:#0a3d82;
  --navy:#0b2c57;
  --orange:#f37122;
  --green:#9bcb3c;
  --lime:#a6d83a;
  --grey-bg:#e8e8e8;
  --light-bg:#efefef;
  --ink:#111;
  --text:#333;
  --white:#fff;
  --star:#f5b400;
}
*{margin:0;padding:0;box-sizing:border-box}
html,body{width:1200px;height:3692px;overflow:hidden}
body{position:relative;font-family:"Source Sans 3",Arial,sans-serif;color:var(--text);background:var(--white)}
.abs{position:absolute}
.btn{position:absolute;display:flex;align-items:center;justify-content:center;background:var(--green);color:var(--navy);font-weight:700;font-size:13px;border-radius:20px;text-transform:uppercase;letter-spacing:.2px}
.section-title{position:absolute;font-weight:900;color:var(--ink);text-transform:uppercase;font-size:42px;line-height:1;letter-spacing:.5px}
.center{left:0;width:1200px;text-align:center}
.para{position:absolute;font-size:14px;line-height:19.5px;color:#222}
.photo{position:absolute}

/* header + hero */
.hero{position:absolute;left:0;top:0;width:1200px;height:637px;background:var(--blue);overflow:hidden}
.hero-photo{position:absolute;inset:0;background:linear-gradient(160deg,#dfe4ea 0%,#f4f6f8 45%,#c9d0d8 100%);clip-path:polygon(384px 63px,1200px 63px,1200px 637px,703px 637px)}
.hero-photo::after{content:"";position:absolute;inset:0;background:radial-gradient(ellipse 260px 180px at 900px 330px,rgba(214,58,46,.55),transparent 70%)}
.hero-stripe{position:absolute;inset:0;background:var(--orange);clip-path:polygon(378px 63px,384px 63px,703px 637px,697px 637px)}
.topbar{position:absolute;left:0;top:0;width:1200px;height:63px;background:var(--blue)}
.brand{position:absolute;left:93px;top:13px;font-weight:700;font-size:16.5px;line-height:16px}
.brand .l1{color:var(--lime)}
.brand .l2{color:var(--white)}
.nav{position:absolute;top:21px;font-size:13px;color:var(--white)}
.nav.active{color:var(--lime)}
.hero-kicker{position:absolute;left:90px;top:228px;font-size:38px;color:var(--white);font-weight:400}
.hero-title{position:absolute;left:90px;top:268px;font-size:86px;line-height:72px;font-weight:900;color:var(--white)}
.dots{position:absolute;display:flex;gap:6px}
.dots i{width:8px;height:8px;border-radius:50%;background:rgba(255,255,255,.35)}
.dots i.on{background:var(--white)}

/* ticker */
.ticker{position:absolute;left:0;top:747px;width:1200px;height:29px;background:var(--orange);color:var(--white);font-weight:700;font-size:15px;display:flex;align-items:center;padding-left:95px;letter-spacing:.2px}
.ticker .src{margin-right:12px}

/* bands */
.band-grey{position:absolute;left:0;width:1200px;background:var(--grey-bg)}
.cv-band{position:absolute;left:0;top:1222px;width:1200px;height:178px;background:radial-gradient(ellipse at 50% 50%,#1d6bc4 0%,#0d4c98 55%,#072f66 100%)}
.reviews{position:absolute;left:0;top:1844px;width:1200px;height:534px;background:radial-gradient(ellipse at 50% 40%,#242424 0%,#0d0d0d 70%,#050505 100%)}
.review-card{position:absolute;top:1997px;width:323px;height:276px;background:var(--white)}
.avatar{position:absolute;left:28px;top:-28px;width:92px;height:92px;border-radius:50%;background:linear-gradient(160deg,#d8d8d8,#a9a9a9);border:3px solid var(--white);box-shadow:0 1px 4px rgba(0,0,0,.3)}
.review-name{position:absolute;left:27px;top:87px;font-size:16.5px;color:#222}
.review-role{position:absolute;left:27px;top:108px;font-size:11.5px;color:#555}
.review-text{position:absolute;left:27px;top:134px;width:268px;font-size:11.5px;line-height:16.5px;color:#222}
.see-more{position:absolute;left:27px;top:188px;font-size:11px;font-weight:700;color:var(--blue)}
.stars{position:absolute;left:25px;top:228px;font-size:14px;color:var(--star);letter-spacing:1px}
.quote{position:absolute;right:10px;top:188px;font-size:120px;line-height:1;font-weight:900;color:#fbe2d4;font-family:Georgia,serif}

.media{position:absolute;left:0;top:2378px;width:1200px;height:497px;background:var(--light-bg)}
.media-thumb{position:absolute;top:2528px;width:329px;height:173px;box-shadow:0 2px 4px rgba(0,0,0,.25)}
.media-caption{position:absolute;top:2713px;width:320px;font-size:14.5px;line-height:20px;font-weight:700;color:#222}
.media-date{position:absolute;top:2758px;font-size:12.5px;color:#444;display:flex;align-items:center;gap:6px}

.tile{position:absolute;width:300px;height:216px}
.tile-text{background:var(--white)}
.tile-title{position:absolute;left:35px;top:50px;font-size:26px;font-weight:700;color:var(--orange);letter-spacing:.3px}
.tile-body{position:absolute;left:37px;top:86px;width:170px;font-size:11.5px;line-height:15.5px;color:#444}
.tile-more{position:absolute;left:37px;top:152px;font-size:11px;font-weight:700;color:#111;letter-spacing:.5px}

/* footer */
.footer{position:absolute;left:0;top:3307px;width:1200px;height:385px;background:var(--blue-deep);overflow:hidden}
.footer-left{position:absolute;inset:0;background:#0b52a3;clip-path:polygon(0 0,416px 0,631px 385px,0 385px)}
.footer-line{position:absolute;inset:0;background:var(--orange);clip-path:polygon(415px 0,418px 0,633px 385px,630px 385px)}
.f-head{position:absolute;font-size:16px;font-weight:700;color:var(--white);letter-spacing:.3px}
.f-link{position:absolute;font-size:14px;color:#e8eef8}
.f-link.active{color:var(--lime)}
.f-row{position:absolute;left:93px;display:flex;gap:14px;color:#e8eef8;font-size:14px;line-height:19px}
.f-input{position:absolute;left:652px;top:3540px;width:335px;height:33px;background:var(--white);border-radius:18px;font-size:10.5px;font-weight:700;color:#222;padding-left:18px;display:flex;align-items:center}
</style>
</head>
<body>

<!-- Hero -->
<section class="hero">
  <div class="hero-photo" role="img" aria-label="Photo of rescuers in red jackets tending a patient on a sled in a snowy forest"></div>
  <div class="hero-stripe"></div>
  <div class="topbar"></div>
  <div class="brand"><div class="l1">Wilderness and EMS</div><div class="l2">Emergency Physician</div></div>
  <div class="nav active" style="left:627px">Home</div>
  <div class="nav" style="left:697px">Experience</div>
  <div class="nav" style="left:796px">Consulting</div>
  <div class="nav" style="left:893px">Lectures</div>
  <div class="nav" style="left:979px">Affiliates</div>
  <div class="nav" style="left:1064px">Contact</div>
  <div class="hero-kicker">Emergency Physician</div>
  <div class="hero-title">BASED ON<br>Wilderness</div>
  <div class="btn" style="left:93px;top:426px;width:106px;height:36px">Read More</div>
  <div class="dots" style="left:94px;top:590px"><i class="on"></i><i></i><i></i></div>
</section>

<!-- Intro -->
<div class="section-title center" style="top:667px">Lorem Ipsum Dollar</div>
<div class="abs center" style="top:710px;font-size:16px;color:#222">The point of using Lorem Ipsum is that it has a more-or-less normal distribution of letters,</div>

<div class="ticker">
  <span class="src">WNN</span>NEWS&nbsp; 03:06 THE POINT OF USING LOREM IPSUM IS THAT IT HAS A MORE-OR-LESS NORMAL DISTRIBUTION
  <svg class="abs" style="left:1084px;top:6px" width="22" height="18" viewBox="0 0 22 18" fill="none" stroke="#fff" stroke-width="1.6"><rect x="1.5" y="5" width="19" height="11.5" rx="1.5"/><path d="M7 1l4 4 4-4"/></svg>
</div>

<!-- Interviews -->
<section class="band-grey" style="top:776px;height:446px"></section>
<div class="section-title" style="left:93px;top:893px;font-size:40px">My Interviews</div>
<p class="para" style="left:94px;top:942px;width:400px">Lorem ipsum dolor sit amet, consectetur adipiscing elit. Etiam nec ultricies leo, sit amet dignissim arcu. Nulla et malesuada enim. Donec congue nec felis at consequat. Vestibulum sit amet efficitur odio, ut luctus enim. Ut vestibulum laoreet lacus ut fermentum. Nunc a diam vel lectus varius imperdiet a ut metus.</p>
<div class="btn" style="left:95px;top:1053px;width:106px;height:36px">View More</div>
<div class="photo" style="left:538px;top:822px;width:569px;height:358px;background:linear-gradient(135deg,#1b2a44 0%,#2c3f63 50%,#1e4c8f 100%)" role="img" aria-label="Television news studio still with two presenters"></div>

<!-- CV -->
<section class="cv-band"></section>
<div class="section-title center" style="top:1264px;color:var(--white)">Take a Look at My CV</div>
<div class="btn" style="left:546px;top:1319px;width:106px;height:35px">Download</div>

<!-- Teachings -->
<section class="band-grey" style="top:1400px;height:444px"></section>
<div class="photo" style="left:96px;top:1444px;width:569px;height:357px;background:linear-gradient(120deg,#6c5a8c 0%,#d8dde2 40%,#eef0f2 70%,#b8bcc2 100%)" role="img" aria-label="Classroom photo of trainees in white coats practising CPR on a manikin"></div>
<div class="section-title" style="left:715px;top:1514px;font-size:40px">My Teachings</div>
<p class="para" style="left:717px;top:1563px;width:400px">Lorem ipsum dolor sit amet, consectetur adipiscing elit. Etiam nec ultricies leo, sit amet dignissim arcu. Nulla et malesuada enim. Donec congue nec felis at consequat. Vestibulum sit amet efficitur odio, ut luctus enim. Ut vestibulum laoreet lacus ut fermentum. Nunc a diam vel lectus varius imperdiet a ut metus.</p>
<div class="btn" style="left:717px;top:1675px;width:115px;height:36px">View Course</div>

<!-- Reviews -->
<section class="reviews"></section>
<div class="section-title center" style="top:1897px;color:var(--white)">Lecture Reviews</div>

<div class="review-card" style="left:93px">
  <div class="avatar" role="img" aria-label="Reviewer portrait"></div>
  <div class="review-name">Lorem Ipsum</div>
  <div class="review-role">Mauris posuere lobortis</div>
  <div class="review-text">Lorem ipsum dolor sit amet, consectetur adipiscing elit. Mauris posuere lobortis leo ut egestas. Integer pharetra, risus ac feugiat laoreet.</div>
  <div class="see-more">See More</div>
  <div class="stars">★★★★★</div>
  <div class="quote">“</div>
</div>
<div class="review-card" style="left:437px">
  <div class="avatar" role="img" aria-label="Reviewer portrait"></div>
  <div class="review-name">Lorem Ipsum</div>
  <div class="review-role">Mauris posuere lobortis</div>
  <div class="review-text">Lorem ipsum dolor sit amet, consectetur adipiscing elit. Mauris posuere lobortis leo ut egestas. Integer pharetra, risus ac feugiat laoreet.</div>
  <div class="see-more">See More</div>
  <div class="stars">★★★★★</div>
  <div class="quote">“</div>
</div>
<div class="review-card" style="left:781px">
  <div class="avatar" role="img" aria-label="Reviewer portrait"></div>
  <div class="review-name">Lorem Ipsum</div>
  <div class="review-role">Mauris posuere lobortis</div>
  <div class="review-text">Lorem ipsum dolor sit amet, consectetur adipiscing elit. Mauris posuere lobortis leo ut egestas. Integer pharetra, risus ac feugiat laoreet.</div>
  <div class="see-more">See More</div>
  <div class="stars">★★★★★</div>
  <div class="quote">“</div>
</div>
<div class="btn" style="left:548px;top:2291px;width:105px;height:35px">View More</div>

<!-- Popular media -->
<section class="media"></section>
<div class="section-title center" style="top:2462px">Popular Media</div>

<div class="media-thumb" style="left:95px;background:linear-gradient(135deg,#6d6a66,#b9bfc6 60%,#8d96a0)" role="img" aria-label="Video still of a rocky mountain ledge"></div>
<div class="media-thumb" style="left:436px;background:linear-gradient(135deg,#4d5a3a,#8a7a5a 50%,#a84f4a)" role="img" aria-label="Video still of hikers treating an injury on a trail"></div>
<div class="media-thumb" style="left:777px;background:linear-gradient(135deg,#9fb3c8,#e4ecf2 50%,#c23b36)" role="img" aria-label="Video still of climbers on an ice wall"></div>
<svg class="abs" style="left:232px;top:2594px" width="40" height="44" viewBox="0 0 40 44"><path d="M2 2l36 20L2 42z" fill="rgba(255,255,255,.7)"/></svg>
<svg class="abs" style="left:582px;top:2594px" width="40" height="44" viewBox="0 0 40 44"><path d="M2 2l36 20L2 42z" fill="rgba(255,255,255,.7)"/></svg>
<svg class="abs" style="left:930px;top:2594px" width="40" height="44" viewBox="0 0 40 44"><path d="M2 2l36 20L2 42z" fill="rgba(255,255,255,.7)"/></svg>

<div class="media-caption" style="left:94px">Lorem ipsum dolor sit amet, consectetur adipiscing elit.</div>
<div class="media-caption" style="left:435px">Lorem ipsum dolor sit amet, consectetur adipiscing elit.</div>
<div class="media-caption" style="left:775px">Lorem ipsum dolor sit amet, consectetur adipiscing elit.</div>
<div class="media-date" style="left:94px"><svg width="11" height="11" viewBox="0 0 12 12" fill="none" stroke="#555" stroke-width="1.3"><circle cx="6" cy="6" r="5"/><path d="M6 3v3l2 1.5"/></svg>11 Dec 2019</div>
<div class="media-date" style="left:435px"><svg width="11" height="11" viewBox="0 0 12 12" fill="none" stroke="#555" stroke-width="1.3"><circle cx="6" cy="6" r="5"/><path d="M6 3v3l2 1.5"/></svg>11 Dec 2019</div>
<div class="media-date" style="left:775px"><svg width="11" height="11" viewBox="0 0 12 12" fill="none" stroke="#555" stroke-width="1.3"><circle cx="6" cy="6" r="5"/><path d="M6 3v3l2 1.5"/></svg>11 Dec 2019</div>
<div class="abs" style="left:584px;top:2801px;display:flex;gap:6px"><i style="width:7px;height:7px;border-radius:50%;background:#111"></i><i style="width:7px;height:7px;border-radius:50%;background:#ccc"></i><i style="width:7px;height:7px;border-radius:50%;background:#ccc"></i></div>

<!-- Topic tiles -->
<div class="tile" style="left:0;top:2875px;background:linear-gradient(135deg,#e9c7b6,#8fb4d8 60%,#3a78b8)" role="img" aria-label="Photo of a bandaged knee being treated"></div>
<div class="tile tile-text" style="left:300px;top:2875px">
  <div class="tile-title">RESEARCH</div>
  <div class="tile-body">Lorem ipsum dolor sit amet, consectetur adipiscing elit. Ut et faucibus metus. Aliquam condimentum velit.</div>
  <div class="tile-more">READ MORE</div>
</div>
<div class="tile" style="left:600px;top:2875px;background:linear-gradient(135deg,#3f4c5c,#c9d4de 50%,#2c3e55)" role="img" aria-label="Photo of a television control room with monitors"></div>
<div class="tile tile-text" style="left:900px;top:2875px">
  <div class="tile-title">EXPLORATION</div>
  <div class="tile-body">Lorem ipsum dolor sit amet, consectetur adipiscing elit. Ut et faucibus metus. Aliquam condimentum velit.</div>
  <div class="tile-more">READ MORE</div>
</div>
<div class="tile tile-text" style="left:0;top:3091px">
  <div class="tile-title">TRAINING</div>
  <div class="tile-body">Lorem ipsum dolor sit amet, consectetur adipiscing elit. Ut et faucibus metus. Aliquam condimentum velit.</div>
  <div class="tile-more">READ MORE</div>
</div>
<div class="tile" style="left:300px;top:3091px;background:linear-gradient(180deg,#c8ccd2,#eef0f2 45%,#dfe3e7)" role="img" aria-label="Photo of ski patrol towing a rescue sled on a slope"></div>
<div class="tile tile-text" style="left:600px;top:3091px">
  <div class="tile-title">TELEVISION</div>
  <div class="tile-body">Lorem ipsum dolor sit amet, consectetur adipiscing elit. Ut et faucibus metus. Aliquam condimentum velit.</div>
  <div class="tile-more">READ MORE</div>
</div>
<div class="tile" style="left:900px;top:3091px;background:linear-gradient(180deg,#1c3f86,#6e86b8 50%,#3a3328)" role="img" aria-label="Photo of a mountain summit above the clouds"></div>

<!-- Footer -->
<footer class="footer">
  <div class="footer-left"></div>
  <div class="footer-line"></div>
</footer>
<div class="f-head" style="left:93px;top:3408px">CONTACT US</div>
<div class="f-row" style="top:3444px">
  <svg width="12" height="16" viewBox="0 0 12 16" style="margin-top:3px"><path d="M6 0a6 6 0 0 0-6 6c0 4.5 6 10 6 10s6-5.5 6-10a6 6 0 0 0-6-6zm0 8.2A2.2 2.2 0 1 1 6 3.8a2.2 2.2 0 0 1 0 4.4z" fill="#fff"/></svg>
  <div>US Office<br>Address: 48 Timberline Way<br>Cedar Hollow, ST 00000</div>
</div>
<div class="f-row" style="top:3512px">
  <svg width="12" height="12" viewBox="0 0 12 12" style="margin-top:4px"><path d="M2.5 0.5l2 2.5-1.2 1.5a7 7 0 0 0 4.2 4.2L9 7.5l2.5 2-1.5 2C5 11.5 0.5 7 0.5 2z" fill="#fff"/></svg>
  <div>Telephone: 555-014-2290</div>
</div>
<div class="f-row" style="top:3548px">
  <svg width="12" height="10" viewBox="0 0 12 10" style="margin-top:5px"><rect width="12" height="10" rx="1" fill="#fff"/><path d="M0.5 1l5.5 4.5L11.5 1" stroke="#0b52a3" stroke-width="1.2" fill="none"/></svg>
  <div>Mail : physician@ridgewayhealer.com</div>
</div>

<div class="f-head" style="left:376px;top:3408px">FOLLOW US</div>
<div class="f-link" style="left:376px;top:3438px">Campfire</div>
<div class="f-link" style="left:376px;top:3466px">Snapline</div>
<div class="f-link" style="left:376px;top:3494px">Chirper</div>
<div class="f-link" style="left:376px;top:3522px">Streamtube</div>
<div class="f-link" style="left:376px;top:3550px">Careerlink</div>

<div class="f-head" style="left:652px;top:3408px">QUICK LINK</div>
<div class="f-link active" style="left:652px;top:3439px">Home</div>
<div class="f-link" style="left:714px;top:3439px">Experience</div>
<div class="f-link" style="left:806px;top:3439px">Consulting</div>
<div class="f-link" style="left:896px;top:3439px">Lectures</div>
<div class="f-link" style="left:976px;top:3439px">Affiliates</div>
<div class="f-link" style="left:1054px;top:3439px">Contact</div>

<div class="f-head" style="left:652px;top:3502px">SUBSCRIBE NEWSLETTER</div>
<div class="f-input">ENTER YOUR MAIL ID</div>
<div class="btn" style="left:652px;top:3581px;width:107px;height:35px">Subscribe</div>

<div class="f-link" style="left:95px;top:3604px">Copyright©2019 emergency physician. All Rights Reserved.</div>

</body>
</html>
```